Gobal construction supply company needs new business card design

I need a business card design for my global supply company using an existing logo. i will be looking to print these on rounded corner cards with the black background version of my logo on the back. on the front white background, my logo again and my simple details.

```html
<!DOCTYPE html>
<html lang="en">
<head>
<meta charset="utf-8">
<title>Northgate Supply Group – Business Card</title>
<link rel="stylesheet" href="https://fonts.googleapis.com/css2?family=Montserrat:wght@700&family=Work+Sans:wght@400;500&display=swap">
<style>
  :root {
    --backdrop: #1c1c1d;
    --card: #1f1f20;
    --card-deep: #161617;
    --pattern-a: #2a2a2b;
    --pattern-b: #3a3a3b;
    --ink: #ffffff;
    --ink-soft: #e4e4e4;
    --accent: #e3161e;
    --rule: #d8d8d8;
  }
  * { box-sizing: border-box; margin: 0; padding: 0; }
  html, body { width: 1200px; height: 900px; overflow: hidden; }
  body {
    background: var(--backdrop);
    font-family: "Work Sans", Arial, sans-serif;
    color: var(--ink);
    position: relative;
  }
  .card {
    position: absolute;
    left: 290px;
    width: 620px;
    height: 354px;
    border-radius: 6px;
    overflow: hidden;
    box-shadow: 0 18px 40px rgba(0,0,0,0.55);
  }
  .card--back { top: 48px; background: var(--card-deep); }
  .card--front {
    top: 470px;
    background: linear-gradient(160deg, #262627 0%, var(--card) 55%, #1a1a1b 100%);
  }

  /* back */
  .back-pattern {
    position: absolute; inset: 0;
    background: linear-gradient(115deg, var(--pattern-a) 0%, var(--card-deep) 40%, var(--pattern-b) 100%);
  }
  .back-brand {
    position: absolute;
    right: 78px; bottom: 62px;
    display: flex; align-items: center; gap: 8px;
  }
  .brand-name {
    font-family: "Montserrat", Arial, sans-serif;
    font-weight: 700;
    color: var(--ink);
    text-transform: uppercase;
    letter-spacing: 0.02em;
  }
  .back-brand .brand-name { font-size: 15px; }
  .brand-dot {
    display: block; border-radius: 50%; background: var(--accent);
  }
  .back-brand .brand-dot { width: 9px; height: 9px; }

  /* front */
  .front-brand {
    position: absolute;
    left: 40px; top: 0; bottom: 0; width: 250px;
    display: flex; flex-direction: column; justify-content: center; align-items: center;
    gap: 10px; text-align: center;
  }
  .front-brand .brand-dot { width: 22px; height: 22px; }
  .front-brand .brand-name { font-size: 23px; line-height: 1.2; }
  .divider {
    position: absolute;
    left: 320px; top: 82px;
    width: 2px; height: 190px;
    background: var(--rule);
  }
  .contact {
    position: absolute;
    left: 350px; top: 82px;
  }
  .contact__name {
    color: var(--accent);
    font-weight: 500;
    font-size: 23px;
    text-transform: uppercase;
    letter-spacing: 0.02em;
    line-height: 1;
  }
  .contact__role { font-size: 15px; color: var(--ink-soft); margin-top: 4px; letter-spacing: 0.04em; }
  .contact__address { font-size: 15px; line-height: 1.35; margin-top: 16px; letter-spacing: 0.03em; }
  .contact__list { list-style: none; margin-top: 8px; font-size: 15px; letter-spacing: 0.03em; }
  .contact__list li { display: flex; align-items: center; gap: 10px; line-height: 1.45; }
  .icon { width: 11px; height: 11px; flex: none; fill: none; stroke: var(--accent); stroke-width: 1.6; }
  .icon--solid { fill: var(--accent); stroke: none; }
</style>
</head>
<body>
  <section class="card card--back" aria-label="Card back">
    <div class="back-pattern" role="img" aria-label="Tonal repeating brand pattern across the card back"></div>
    <div class="back-brand">
      <span class="brand-name">Northgate Supply Group</span>
      <span class="brand-dot"></span>
    </div>
  </section>

  <section class="card card--front" aria-label="Card front">
    <div class="front-brand">
      <span class="brand-dot"></span>
      <span class="brand-name">Northgate<br>Supply Group</span>
    </div>
    <div class="divider"></div>
    <div class="contact">
      <p class="contact__name">Daniel Reeve</p>
      <p class="contact__role">Director</p>
      <p class="contact__address">48 Harbour Road Box<br>2760, Elm Ridge, AB</p>
      <ul class="contact__list">
        <li>
          <svg class="icon icon--solid" viewBox="0 0 12 12" aria-hidden="true"><path d="M2.4 0.6l2 0.4 0.6 2.6-1.3 1a6.5 6.5 0 0 0 3.7 3.7l1-1.3 2.6 0.6 0.4 2a1 1 0 0 1-1 1.2A10.4 10.4 0 0 1 0.2 1.6 1 1 0 0 1 1.4 0.6z"/></svg>
          403-555-0182
        </li>
        <li>
          <svg class="icon" viewBox="0 0 12 12" aria-hidden="true"><rect x="0.8" y="2.2" width="10.4" height="7.6"/><path d="M0.8 2.4L6 6.6l5.2-4.2"/></svg>
          info@northgatesupply.com
        </li>
        <li>
          <svg class="icon" viewBox="0 0 12 12" aria-hidden="true"><circle cx="6" cy="6" r="5.2"/><ellipse cx="6" cy="6" rx="2.2" ry="5.2"/><path d="M0.8 6h10.4"/></svg>
          www.northgatesupply.com
        </li>
      </ul>
    </div>
  </section>
</body>
</html>
```